BRTL web site redesign

Coastal Linkage Engineering service (BRTL) is a diverse technology company specialising in design and installation of fibre optics, network convergence and building services, for commercial clients in Australia, we required a new design of our website to attract new clients, generate sales leads, and provide information about our services to the market. The site and should have a new technology look and feel and be designed in word press. our branding colour is blue.

Target Market(s)

New developments, Construction organisations, Commercial end users, IT managers, Consultants.

Industry/Entity Type

It Company

Number of Pages Required

5+ page

Font styles to use
Sans Serif

Colors
0292cd
3176b5

Requirements
Must have
• key pages.
• Home page with some sizzle, automated pictures running through, I like the look of this competitor website http://www.gleamwirex.com.au/ good clean menus and easy to navigate.
• Services page our key services are Fibre optics, Security, Building services,Electrical. I would like the same page layout (Design) for all our services, with a find out more link on each page, manly picture driven with text around our key messaging.
• About us page with space for company profile and directors pictures, bio and contact information.
• Certifications / Accreditations page with have over 20 certifications on different products from suppliers, and a number of licences from governing bodies.
• Current and past projects page with case studies and customer outcomes
• Contact us page with options around what services they require more information on, please keep in mind the site is around generating sales Leeds and being seen as an industry expert.
Nice to have
• RSS feeds, Linked in link, to be placed within the design, Consistent BRTL branding,Same colour blue as our logo Document library for education information, white papers, presentations etc,
• a new technology look and feel, mobile friendly.
Should not have
• boring layout, move away from our cuurent website http://www.brtlgroup.com.au/
• no e eCommerce store required.

```html
<!DOCTYPE html>
<html lang="en">
<head>
<meta charset="utf-8">
<title>BRTL – Coastal Linkage Engineering Service</title>
<link rel="stylesheet" href="https://fonts.googleapis.com/css2?family=Arvo:ital,wght@1,700&family=Lato:wght@400;700;900&display=swap">
<style>
:root{
  --brand:#0a82c2;
  --brand-dark:#0877b3;
  --brand-light:#0292cd;
  --ink:#333333;
  --text:#3a3a3a;
  --topbar:#2e2e2e;
  --footer:#343434;
  --footer-rule:#4a4a4a;
  --white:#ffffff;
  --dropdown:#3a3a3a;
  --navy:#142d66;
  --royal:#2a5cb0;
  --cable-yellow:#e4c84a;
  --suit:#1e1f23;
}
*{box-sizing:border-box;margin:0;padding:0}
html,body{width:1200px;height:2691px;overflow:hidden}
body{position:relative;font-family:"Lato",Arial,sans-serif;color:var(--text);background:var(--white)}
.abs{position:absolute}
.heading{font-family:"Arvo",Georgia,serif;font-style:italic;font-weight:700;text-align:center;position:absolute;left:0;width:1200px;font-size:27px}
.heading span{display:inline-block;width:7px;height:7px;border-radius:50%;background:currentColor;vertical-align:middle;margin:0 12px}

/* top bar */
.topbar{left:0;top:0;width:1200px;height:34px;background:var(--topbar);color:#eee;font-size:11px}
.topbar .greet{position:absolute;left:124px;top:10px}
.topbar .social{position:absolute;left:565px;top:11px;display:flex;gap:16px}
.topbar .social i{width:11px;height:11px;border-radius:50%;background:#ddd;display:block}
.topbar .tools{position:absolute;left:758px;top:0;height:34px;display:flex}
.topbar .tools div{height:34px;border-left:1px solid #555;display:flex;align-items:center;gap:6px;padding:0 16px}
.topbar .tools div:last-child{border-right:1px solid #555}

/* header */
.header{left:0;top:34px;width:1200px;height:129px;background:var(--brand)}
.logo{position:absolute;left:124px;top:9px;width:219px;height:114px;background:var(--white);display:flex;flex-direction:column;justify-content:center;padding-left:16px;color:var(--brand-dark);font-weight:900}
.logo .name{font-size:58px;line-height:1;letter-spacing:2px;display:flex;align-items:center;gap:12px}
.logo .name i{width:18px;height:18px;background:var(--brand-dark);display:block}
.logo .tag{font-size:8.4px;letter-spacing:.2px;margin-top:8px;text-transform:uppercase}
.nav{position:absolute;left:440px;top:0;height:129px;display:flex;font-size:14px;color:var(--white)}
.nav a{display:flex;align-items:center;padding:0 19px;color:inherit;text-decoration:none}
.nav a.active{background:var(--white);color:var(--brand);padding:0 14px}
.dropdown{left:520px;top:163px;width:97px;background:var(--dropdown);font-size:10.5px;z-index:3}
.dropdown div{height:35px;line-height:35px;padding-left:10px;color:#aaa;border-bottom:1px solid #2c2c2c}
.dropdown div.current{background:var(--brand);color:var(--white)}

/* hero */
.hero{left:0;top:163px;width:1200px;height:517px;
  background:
    radial-gradient(ellipse 70px 260px at 215px 170px,rgba(240,205,60,.95),rgba(240,205,60,0) 100%),
    radial-gradient(ellipse 45px 200px at 150px 120px,rgba(235,200,70,.7),rgba(235,200,70,0) 100%),
    radial-gradient(ellipse 60px 240px at 270px 360px,rgba(220,190,80,.55),rgba(220,190,80,0) 100%),
    radial-gradient(ellipse 140px 420px at 60px 260px,rgba(150,160,170,.55),rgba(150,160,170,0) 100%),
    radial-gradient(ellipse 40px 380px at 630px 200px,rgba(40,90,170,.8),rgba(40,90,170,0) 100%),
    radial-gradient(ellipse 24px 300px at 690px 160px,rgba(20,40,80,.75),rgba(20,40,80,0) 100%),
    radial-gradient(ellipse 60px 120px at 740px 90px,rgba(70,120,200,.6),rgba(70,120,200,0) 100%),
    radial-gradient(ellipse 130px 290px at 975px 390px,rgba(30,31,35,1) 55%,rgba(30,31,35,0) 100%),
    radial-gradient(ellipse 60px 60px at 940px 115px,rgba(200,160,130,.8) 40%,rgba(200,160,130,0) 100%),
    radial-gradient(ellipse 110px 30px at 830px 300px,rgba(220,225,230,.9),rgba(220,225,230,0) 100%),
    linear-gradient(90deg,#dde3e8 0%,#eef1f3 40%,#f4f5f6 60%,#f2f3f4 100%);}

/* welcome */
.welcome-title{top:700px;color:var(--brand)}
.welcome-text{left:204px;top:750px;width:792px;text-align:center;font-size:12.6px;line-height:15px;color:var(--ink)}

/* about */
.about{left:0;top:846px;width:1200px;height:334px;
  background:
    radial-gradient(circle 40px at 120px 40px,rgba(255,255,255,.8),rgba(255,255,255,0)),
    radial-gradient(circle 30px at 300px 20px,rgba(255,255,255,.7),rgba(255,255,255,0)),
    radial-gradient(circle 35px at 420px 60px,rgba(255,255,255,.6),rgba(255,255,255,0)),
    radial-gradient(circle 50px at 40px 300px,rgba(255,255,255,.5),rgba(255,255,255,0)),
    radial-gradient(ellipse 260px 120px at 1060px 260px,rgba(120,160,195,.55),rgba(120,160,195,0)),
    radial-gradient(ellipse 200px 90px at 1100px 60px,rgba(150,185,215,.6),rgba(150,185,215,0)),
    linear-gradient(90deg,#a9c9e2 0%,#d8e7f2 30%,#eaf2f8 55%,#d3e3ee 80%,#b0cde0 100%);}
.about-title{top:872px;color:#1a1a1a}
.about-photo{left:126px;top:930px;width:374px;height:211px;border:3px solid var(--white);
  background:
    radial-gradient(ellipse 50px 90px at 200px 150px,rgba(20,20,28,.95) 50%,rgba(20,20,28,0)),
    radial-gradient(ellipse 80px 40px at 170px 55px,rgba(190,225,255,.8),rgba(190,225,255,0)),
    radial-gradient(ellipse 60px 90px at 340px 90px,rgba(120,180,240,.55),rgba(120,180,240,0)),
    radial-gradient(ellipse 90px 60px at 60px 90px,rgba(80,130,210,.5),rgba(80,130,210,0)),
    linear-gradient(135deg,#173a80 0%,#2a5cb0 50%,#112452 100%);}
.about-text{left:531px;top:926px;width:544px;font-size:12.4px;line-height:15.5px;color:#222;text-align:justify}
.about-text p+p{margin-top:15px}
.btn-solid{left:531px;top:1104px;width:138px;height:39px;background:var(--brand-dark);color:var(--white);font-size:13px;display:flex;align-items:center;justify-content:center;border-radius:3px;box-shadow:0 3px 0 #055b8a}

/* services */
.services{left:0;top:1180px;width:1200px;height:509px;background:var(--brand)}
.services-title{top:1206px;color:var(--white)}
.service{position:absolute;top:1267px;width:300px;color:var(--white)}
.service .photo{width:300px;height:200px;border:3px solid var(--white)}
.photo-security{background:
  radial-gradient(ellipse 55px 30px at 210px 125px,rgba(60,62,68,.95) 55%,rgba(60,62,68,0)),
  radial-gradient(ellipse 70px 40px at 70px 170px,rgba(190,140,90,.85),rgba(190,140,90,0)),
  linear-gradient(90deg,rgba(0,0,0,0) 49%,rgba(255,255,255,.9) 49.5%,rgba(255,255,255,.9) 50.5%,rgba(0,0,0,0) 51%),
  linear-gradient(180deg,#4f7fb8 0%,#a9c3dd 40%,#c9ccce 60%,#8a8f95 100%);}
.photo-fibre{background:
  radial-gradient(ellipse 80px 40px at 90px 120px,rgba(80,170,70,.85),rgba(80,170,70,0)),
  radial-gradient(ellipse 50px 40px at 200px 40px,rgba(205,150,120,.85),rgba(205,150,120,0)),
  radial-gradient(ellipse 40px 30px at 150px 60px,rgba(40,150,220,.8),rgba(40,150,220,0)),
  radial-gradient(ellipse 60px 40px at 230px 150px,rgba(210,120,50,.7),rgba(210,120,50,0)),
  linear-gradient(135deg,#2a2c30 0%,#45484d 50%,#25272a 100%);}
.photo-ict{background:
  radial-gradient(ellipse 150px 28px at 150px 175px,rgba(8,15,40,1) 60%,rgba(8,15,40,0)),
  radial-gradient(ellipse 80px 50px at 150px 80px,rgba(120,200,255,.7),rgba(120,200,255,0)),
  radial-gradient(circle 25px at 50px 40px,rgba(200,235,255,.6),rgba(200,235,255,0)),
  radial-gradient(circle 25px at 250px 50px,rgba(200,235,255,.6),rgba(200,235,255,0)),
  linear-gradient(180deg,#1a4aa3 0%,#2b70d2 55%,#0b1f55 100%);}
.service h3{font-weight:400;font-size:18px;margin-top:12px}
.service p{font-size:12.2px;line-height:14px;margin-top:9px}
.service .btn{margin-top:20px;width:137px;height:34px;background:var(--white);color:var(--brand);font-size:12.5px;font-weight:700;display:flex;align-items:center;justify-content:center;border-radius:3px}
.dots{left:569px;top:1638px;display:flex;gap:11px}
.dots i{width:7px;height:7px;border-radius:50%;background:#bfe0f2;display:block}

/* blog */
.blog-title{top:1714px;color:var(--brand)}
.post{position:absolute;top:1774px;width:300px;height:356px;background:#f1f1f1;box-shadow:0 2px 6px rgba(0,0,0,.35);padding:9px}
.post .photo{height:170px;
  background:
    radial-gradient(ellipse 45px 80px at 155px 125px,rgba(20,20,28,.95) 50%,rgba(20,20,28,0)),
    radial-gradient(ellipse 70px 35px at 130px 40px,rgba(190,225,255,.8),rgba(190,225,255,0)),
    radial-gradient(ellipse 50px 80px at 260px 80px,rgba(120,180,240,.55),rgba(120,180,240,0)),
    radial-gradient(ellipse 70px 50px at 40px 80px,rgba(80,130,210,.5),rgba(80,130,210,0)),
    linear-gradient(135deg,#173a80 0%,#2a5cb0 50%,#112452 100%);}
.post h3{font-weight:400;font-size:18px;color:var(--brand);margin:20px 0 0 6px}
.post .meta{display:flex;gap:12px;font-size:10px;color:#444;margin:12px 0 0 6px;align-items:center}
.post .meta span{display:flex;gap:4px;align-items:center}
.post p{font-size:11.4px;line-height:13px;color:#333;margin:12px 6px 0;text-align:justify}
.post .more{position:absolute;left:15px;right:15px;bottom:26px;height:1px;background:var(--brand)}
.post .more span{position:absolute;right:0;top:-7px;background:#f1f1f1;padding-left:8px;font-size:10.5px;color:var(--brand);display:flex;align-items:center;gap:5px}

/* footer */
.footer{left:0;top:2167px;width:1200px;height:524px;background:var(--footer);color:#ddd}
.footer h4{position:absolute;top:37px;font-family:"Arvo",Georgia,serif;font-style:italic;font-weight:700;font-size:19.5px;color:var(--white)}
.footer .intro{position:absolute;left:124px;top:79px;font-size:11.5px}
.field{position:absolute;background:var(--white);font-size:11px;color:#888;padding:9px 7px}
.submit{position:absolute;left:124px;top:370px;width:119px;height:33px;background:var(--white);color:#222;font-size:11.5px;font-weight:700;display:flex;align-items:center;justify-content:center;border-radius:3px}
.links{position:absolute;top:78px;list-style:none;font-size:14px}
.links li{height:41px;line-height:30px;border-bottom:1px solid var(--footer-rule)}
.tweet{position:absolute;left:857px;width:220px;font-size:12.5px;line-height:20px}
.tweet i{position:absolute;left:0;top:3px;width:17px;height:17px;border-radius:50%;background:var(--white)}
.tweet p{padding-left:34px;word-break:break-all}
.tweet small{display:block;padding-left:0;font-size:10px;color:#aaa;margin-top:7px}
.footer .rule{position:absolute;left:124px;top:448px;width:952px;height:1px;background:var(--footer-rule)}
.footer .copy{position:absolute;left:0;top:480px;width:1200px;text-align:center;font-size:10.5px;color:#aaa}
</style>
</head>
<body>

<div class="abs topbar">
  <span class="greet">Wel come...!!!</span>
  <div class="social"><i></i><i></i><i></i></div>
  <div class="tools">
    <div><svg width="8" height="6" viewBox="0 0 8 6"><path d="M1 1l3 3 3-3" stroke="#ddd" fill="none" stroke-width="1.5"/></svg></div>
    <div><svg width="10" height="10" viewBox="0 0 10 10"><circle cx="5" cy="3" r="2.5" fill="#ddd"/><path d="M0 10c0-4 10-4 10 0z" fill="#ddd"/></svg>My Account</div>
    <div><svg width="8" height="6" viewBox="0 0 8 6"><path d="M1 1l3 3 3-3" stroke="#ddd" fill="none" stroke-width="1.5"/></svg></div>
    <div><svg width="11" height="10" viewBox="0 0 11 10"><path d="M0 1h2l2 6h6l1-4H3" stroke="#ddd" fill="none" stroke-width="1.4"/><circle cx="4.5" cy="9" r="1" fill="#ddd"/><circle cx="9" cy="9" r="1" fill="#ddd"/></svg>My Cart</div>
    <div><svg width="10" height="10" viewBox="0 0 10 10"><path d="M2 0l2 2.5-1.3 1.5a6 6 0 0 0 3.3 3.3L7.5 6 10 8 8.5 10C4 10 0 6 0 1.5z" fill="#ddd"/></svg>1300 555 214</div>
  </div>
</div>

<header class="abs header">
  <div class="logo">
    <div class="name"><span>BRTL</span><i></i></div>
    <div class="tag">Coastal Linkage Engineering Service</div>
  </div>
  <nav class="nav">
    <a>Home</a><a class="active">About Us</a><a>Services</a><a>ISP</a><a>Recent Projects</a><a>Contact Us</a><a>Blog</a>
  </nav>
</header>
<div class="abs dropdown"><div class="current">Sub Item 1</div><div>Sub Item 2</div><div>Sub Item 3</div></div>

<section class="abs hero" role="img" aria-label="Photo: blurred yellow fibre cables and a blue-cabled server rack beside a businessman in a dark suit working on a laptop"></section>

<h2 class="heading welcome-title">Wel Come...!</h2>
<p class="abs welcome-text">BRTL is diversified technology company 100% Australian owned and operated, we provide Communication, Electrical, Security &amp; ICT services for residential and commercial customers. With over 100 years of combined industry knowledge we pride ourselves on innovated solutions that utilises technology advancements which delivers on our customer's expectations.</p>

<section class="abs about" role="img" aria-label="Background: bright network cabling and light bokeh in pale blue"></section>
<h2 class="heading about-title"><span></span>About Us</h2>
<div class="abs about-photo" role="img" aria-label="Photo: businesswoman touching a glowing cloud computing interface"></div>
<div class="abs about-text">
  <p>BRTL is a Communications Integration Company incorporating the expertise of Data and Fibre Optic Communications, ICT and low voltage systems, Security and Application Services, with over five decades of experience and successes in their respected field of expertise. The quality and proven ability of our management and tradespeople, in conjunction with our extensive network of resources, ensures a successful outcome for our clients.</p>
  <p>At BRTL our mission is to maximise the value of the service offered to our clients and perform these services through a well-managed process, focusing on quality, technical reliability and cost effectiveness.It is our commitment to provide service with the highest professional standard of excellence, integrity and efficiency.</p>
</div>
<div class="abs btn-solid">READ MORE</div>

<section class="abs services"></section>
<h2 class="heading services-title"><span></span>Our Service<span></span></h2>
<div class="service" style="left:124px">
  <div class="photo photo-security" role="img" aria-label="Photo collage: office towers, handshake and a security camera"></div>
  <h3>Commercial Security Systems</h3>
  <p>BRTL offers a wide range of IP commercial security solutions, from a small standalone system to our fully integrated enterprise systems,</p>
  <div class="btn">LEARN MORE</div>
</div>
<div class="service" style="left:450px">
  <div class="photo photo-fibre" role="img" aria-label="Photo: technician splicing coloured fibre optic cables"></div>
  <h3>Data &amp; Fibre Installations</h3>
  <p>BRTL offers a wide range of IP commercial security solutions, from a small standalone system to our fully integrated enterprise systems,</p>
  <div class="btn">LEARN MORE</div>
</div>
<div class="service" style="left:776px">
  <div class="photo photo-ict" role="img" aria-label="Illustration: business meeting silhouettes under a glowing network globe"></div>
  <h3>Information Com. &amp; Technology</h3>
  <p>BRTL offers a wide range of IP commercial security solutions, from a small standalone system to our fully integrated enterprise systems,</p>
  <div class="btn">LEARN MORE</div>
</div>
<div class="abs dots"><i></i><i></i><i></i><i></i></div>

<h2 class="heading blog-title"><span></span>Our Blog<span></span></h2>
<article class="post" style="left:124px">
  <div class="photo" role="img" aria-label="Photo: businesswoman touching a cloud computing interface"></div>
  <h3>Commercial Security Systems</h3>
  <div class="meta">
    <span><svg width="9" height="9" viewBox="0 0 10 10"><circle cx="5" cy="3" r="2.5" fill="#444"/><path d="M0 10c0-4 10-4 10 0z" fill="#444"/></svg>Lena Marsh</span>
    <span><svg width="9" height="9" viewBox="0 0 10 10"><path d="M0 0h5l5 5-5 5-5-5z" fill="#444"/></svg>Getting Started</span>
    <span><svg width="9" height="9" viewBox="0 0 10 10"><rect x="0" y="1" width="10" height="9" fill="#444"/><rect x="1" y="4" width="8" height="5" fill="#f1f1f1"/></svg>3 months ago</span>
  </div>
  <p>Lorem Ipsum as their default model text, and a search for 'lorem ipsum' will uncover many web sites still in their infancy. lorem ipsum as their</p>
  <div class="more"><span>READ MORE <svg width="11" height="7" viewBox="0 0 11 7"><path d="M0 3.5h9M7 1l3 2.5L7 6" stroke="currentColor" fill="none" stroke-width="1.4"/></svg></span></div>
</article>
<article class="post" style="left:450px">
  <div class="photo" role="img" aria-label="Photo: businesswoman touching a cloud computing interface"></div>
  <h3>Commercial Security Systems</h3>
  <div class="meta">
    <span><svg width="9" height="9" viewBox="0 0 10 10"><circle cx="5" cy="3" r="2.5" fill="#444"/><path d="M0 10c0-4 10-4 10 0z" fill="#444"/></svg>Lena Marsh</span>
    <span><svg width="9" height="9" viewBox="0 0 10 10"><path d="M0 0h5l5 5-5 5-5-5z" fill="#444"/></svg>Getting Started</span>
    <span><svg width="9" height="9" viewBox="0 0 10 10"><rect x="0" y="1" width="10" height="9" fill="#444"/><rect x="1" y="4" width="8" height="5" fill="#f1f1f1"/></svg>3 months ago</span>
  </div>
  <p>Lorem Ipsum as their default model text, and a search for 'lorem ipsum' will uncover many web sites still in their infancy. lorem ipsum as their</p>
  <div class="more"><span>READ MORE <svg width="11" height="7" viewBox="0 0 11 7"><path d="M0 3.5h9M7 1l3 2.5L7 6" stroke="currentColor" fill="none" stroke-width="1.4"/></svg></span></div>
</article>
<article class="post" style="left:776px">
  <div class="photo" role="img" aria-label="Photo: businesswoman touching a cloud computing interface"></div>
  <h3>Commercial Security Systems</h3>
  <div class="meta">
    <span><svg width="9" height="9" viewBox="0 0 10 10"><circle cx="5" cy="3" r="2.5" fill="#444"/><path d="M0 10c0-4 10-4 10 0z" fill="#444"/></svg>Lena Marsh</span>
    <span><svg width="9" height="9" viewBox="0 0 10 10"><path d="M0 0h5l5 5-5 5-5-5z" fill="#444"/></svg>Getting Started</span>
    <span><svg width="9" height="9" viewBox="0 0 10 10"><rect x="0" y="1" width="10" height="9" fill="#444"/><rect x="1" y="4" width="8" height="5" fill="#f1f1f1"/></svg>3 months ago</span>
  </div>
  <p>Lorem Ipsum as their default model text, and a search for 'lorem ipsum' will uncover many web sites still in their infancy. lorem ipsum as their</p>
  <div class="more"><span>READ MORE <svg width="11" height="7" viewBox="0 0 11 7"><path d="M0 3.5h9M7 1l3 2.5L7 6" stroke="currentColor" fill="none" stroke-width="1.4"/></svg></span></div>
</article>

<footer class="abs footer">
  <h4 style="left:124px">Contact BRTL</h4>
  <p class="intro">Please contact us on 1300 555 214 or fill out below</p>
  <div class="field" style="left:124px;top:111px;width:146px;height:33px">First Name</div>
  <div class="field" style="left:278px;top:111px;width:146px;height:33px">Last Name</div>
  <div class="field" style="left:124px;top:155px;width:300px;height:34px">Email Address</div>
  <div class="field" style="left:124px;top:200px;width:300px;height:33px">Primary Contact Phone</div>
  <div class="field" style="left:124px;top:244px;width:300px;height:111px">How can we help you today?</div>
  <div class="submit">SUBMIT</div>

  <h4 style="left:450px">My Account</h4>
  <ul class="links" style="left:450px;width:136px">
    <li>My Account</li><li>Sign In</li><li>Order Status</li><li>My Cart</li><li>My Wishlist</li>
  </ul>

  <h4 style="left:613px">Information</h4>
  <ul class="links" style="left:613px;width:216px;padding-left:24px">
    <li>About Us</li><li>Services</li><li>ISP</li><li>Recent Projects</li><li>Contact Us</li><li>Blog</li>
  </ul>

  <h4 style="left:857px">Latest Tweets</h4>
  <div class="tweet" style="top:88px"><i></i><p>Harbor has now a Vantage versi on - http://lnk.example/Qx4Tr9</p><small>01:53 AM Dec 19th</small></div>
  <div class="tweet" style="top:170px"><i></i><p>Harbor has now a Vantage versi on - http://lnk.example/Qx4Tr9</p><small>01:53 AM Dec 19th</small></div>
  <div class="tweet" style="top:252px"><i></i><p>Harbor has now a Vantage versi on - http://lnk.example/Qx4Tr9</p><small>01:53 AM Dec 19th</small></div>

  <div class="rule"></div>
  <p class="copy">Copyright 2015 BRTL Group. All Rights Reserved. Sitemap</p>
</footer>

</body>
</html>
```